Redesign of outdated "Automotive Automation Company"

We are looking to finally update our outdated website with some cutting edge graphics. We want our customers to know we value technology and are cutting edge as far as design. We provide automation solutions for the automotive industry which essentially means we program robots, and sell automation related products.

Current URL

http://lnk.qorvi.example/Tm4pzr
Updates

Project Deadline Extended
Reason: The client portal wasn't working, it's just finally been fixed by Pixel Harbor. I will go through and start reviewing designs.

We are trying to go with the same look and feel on our business cards, line cards, apparel, etc. so we are forming a brand. I have included the current draft of the line card. Please utilize our newest Logo VEL Standardized Logo.jpg http://img.plomtra.example/zuKe9rb.jpg?1 Also we are trying hard to sell the following software / hardware companies so we can put some emphasis on their product. Corvane Systems https://www.corvanesystems.example/ We make money on selling the software and then on the integration. I think you should tie in this animation. ยท Shop Line Muddle to Momentum https://media.vuntelo.example/clips/9b2e7f1d04c3a85e6f2d1b7c9a0e4f3d8c6b2a1e.jpg?image_play_button=true&image_play_button_color=7b796ae0&image_crop_resized=275x155 In this 2-minute video, discover how Trellan can help run your plant floor. We are Authorized Integrators / Resellers for Pembry Controls Hadrix Sensorik http://hadrix.example/en/usa/ Corvane Systems https://www.corvanesystems.example/ Unified Motion Works www.umwkq.example Brisk Beltway Corp www.briskbeltway.example Castmere Fabrication http://www.castmerefab.example/strategic_partners.aspx

Target Market(s)

Large automotive companies looking for automation or robotic programming. So Professional is key.

Industry/Entity Type

Automotive

Font styles to use
Other font styles liked:
• Possible Open Sans or Lato

Colors
0591cc
ceeaf6
fbd4d5
fbf289
fece3e

Requirements
Must have
• Professional Modern Design.

I want a homepage design, and a rough Sales Page... Where numerous products can be listed.
Nice to have
• Maybe an updated logo if possible.

```html
<!DOCTYPE html>
<html lang="en">
<head>
<meta charset="utf-8">
<title>VEL Engineering Solutions</title>
<link href="https://fonts.googleapis.com/css2?family=Cinzel:wght@600;700&family=Open+Sans:wght@400;600;700&display=swap" rel="stylesheet">
<style>
  :root{
    --sky:#d5ebf7;
    --band:#d2eaf6;
    --blue:#0591cc;
    --blue-deep:#0a73b8;
    --green:#7dbb32;
    --gold:#fece3e;
    --gold-dark:#c7a424;
    --amber:#e6a912;
    --ink:#2b2b2b;
    --text:#3a3a3a;
    --phone:#1a6ea3;
  }
  *{box-sizing:border-box;margin:0;padding:0}
  html,body{width:924px;height:1200px;overflow:hidden;background:#fff}
  body{position:relative;font-family:"Open Sans",Arial,sans-serif;color:var(--text)}
  .abs{position:absolute}

  .site-header{left:0;top:0;width:924px;height:94px;background:var(--sky)}
  .brand{display:flex;align-items:center;gap:8px;font-weight:700;font-size:30px;color:var(--ink)}
  .brand-dot{width:22px;height:22px;border-radius:50%;background:var(--blue)}
  .site-header .brand{left:80px;top:26px}
  .header-phone{left:440px;top:28px;display:flex;align-items:center;gap:8px;font-size:17px;color:var(--phone)}
  .social{left:670px;top:32px;display:flex;gap:10px}
  .social span{width:16px;height:16px;border-radius:50%;background:#8a8f95}

  .main-nav{left:0;top:94px;width:924px;height:34px;background:var(--green);display:flex;padding-left:70px}
  .main-nav a{display:block;height:34px;line-height:34px;padding:0 28px;font-size:12px;letter-spacing:1px;color:#1f2a12;text-decoration:none;border-right:1px solid rgba(255,255,255,.5);font-weight:600}
  .main-nav a:last-child{border-right:none}

  .hero{left:0;top:128px;width:924px;height:289px;background:radial-gradient(ellipse at 75% 40%,#2aa7e4 0%,var(--blue) 45%,var(--blue-deep) 100%)}
  .hero-title{left:92px;top:52px;font-family:"Cinzel",serif;font-weight:700;font-size:48px;color:#fff;letter-spacing:2px}
  .hero-sub{left:100px;top:112px;font-family:"Cinzel",serif;font-weight:600;font-size:17px;line-height:23px;color:#fff;letter-spacing:1.2px}
  .hero-btn{left:99px;top:177px;width:216px;height:46px;background:var(--gold-dark);border-radius:4px;box-shadow:0 3px 0 #8c731a;color:#fff;font-family:"Cinzel",serif;font-weight:700;font-size:17px;letter-spacing:1px;text-align:center;line-height:46px}
  .hero-figure{left:612px;top:78px;width:196px;height:322px;border-radius:60px 60px 30px 30px;background:linear-gradient(160deg,#e9ecef,#9aa1a8 60%,#4b5056)}

  .overview-title{left:90px;top:452px;font-family:"Cinzel",serif;font-weight:700;font-size:28px;letter-spacing:2px;color:var(--ink)}
  .service{left:87px;display:flex;gap:20px;width:400px}
  .service-icon{flex:none;width:75px;height:75px;border-radius:50%;border:2px solid var(--gold);display:flex;align-items:center;justify-content:center}
  .service-icon svg{width:63px;height:63px}
  .service h3{margin-top:12px;font-size:12.5px;font-weight:600;letter-spacing:.3px;color:var(--ink)}
  .service p{margin-top:6px;font-family:Arial,sans-serif;font-size:11px;line-height:14px;color:#333}

  .divider{left:512px;top:460px;width:3px;height:425px;background:linear-gradient(#fff,#e0e0e0 50%,#fff)}

  .intro{left:547px;top:458px;width:290px}
  .intro h2{font-size:13px;font-weight:600;line-height:20px;color:var(--ink)}
  .intro .tagline{margin-top:8px;font-size:11.5px;font-weight:600;color:var(--amber)}
  .intro p{margin-top:11px;font-family:Arial,sans-serif;font-size:11px;line-height:18.4px;color:#444}
  .intro h2.philosophy{margin-top:20px;font-size:17px;font-weight:400}
  .intro p.philosophy-text{margin-top:8px}

  .feature-band{left:0;top:922px;width:924px;height:214px;background:var(--band)}
  .feature{top:31px;width:218px;height:145px;border:2px solid #9aa4ab;overflow:hidden}
  .feature .media{width:100%;height:117px}
  .feature .caption{height:26px;background:rgba(125,187,50,.92);font-size:12.5px;line-height:26px;padding-left:14px;color:#1d2a10}

  .site-footer{left:0;top:1136px;width:924px;height:64px;background:var(--blue)}
  .footer-links{left:90px;top:14px;font-size:11.5px;color:#143a5a;word-spacing:2px}
  .footer-links span{margin:0 12px}
  .copyright{left:90px;top:39px;font-size:11px;color:#143a5a}
  .site-footer .brand{left:725px;top:16px;font-size:24px}
</style>
</head>
<body>

<header class="site-header abs">
  <div class="brand abs"><span class="brand-dot"></span>VEL</div>
  <div class="header-phone abs">
    <svg width="30" height="22" viewBox="0 0 30 22"><path d="M3 8c4-6 20-6 24 0l-4 3-3-3H10l-3 3z" fill="#222"/><rect x="8" y="11" width="14" height="10" rx="3" fill="#f2c20c"/><circle cx="15" cy="16" r="3" fill="#fff"/></svg>
    +123 555 014 200
  </div>
  <div class="social abs"><span></span><span></span><span></span><span></span><span></span><span></span></div>
</header>

<div class="hero abs">
  <div class="hero-title abs">Your Premier</div>
  <div class="hero-sub abs">Automation Consulting &amp; Systems<br>Integration choice!</div>
  <div class="hero-btn abs">1-855-DRIVE-GO</div>
</div>

<nav class="main-nav abs">
  <a href="#">HOME PAGE</a><a href="#">SERVICES</a><a href="#">CONTACT</a><a href="#">ABOUT</a>
</nav>

<div class="hero-figure abs" role="img" aria-label="Silver cartoon robot with a camera-eye head, pondering with hand on chin"></div>

<h2 class="overview-title abs">Overview...</h2>

<div class="service abs" style="top:511px">
  <div class="service-icon"><svg viewBox="0 0 63 63"><circle cx="31.5" cy="31.5" r="31.5" fill="#fece3e"/><path d="M20 44l5-12 18-14 3 3-14 18z" fill="#1b1b1b"/><path d="M20 20l23 23" stroke="#1b1b1b" stroke-width="4" stroke-linecap="round"/></svg></div>
  <div><h3>DESIGN ENGINEERING</h3><p>Provide electro-mechanical designs for machine sizing calcula-tions for motion control and fluid power applications.</p></div>
</div>
<div class="service abs" style="top:606px">
  <div class="service-icon"><svg viewBox="0 0 63 63"><circle cx="31.5" cy="31.5" r="31.5" fill="#fece3e"/><path d="M34 15l-10 19h8l-4 15 12-21h-8z" fill="#1b1b1b"/><g stroke="#1b1b1b" stroke-width="3" stroke-linecap="round"><path d="M14 31h5M44 31h5M19 19l4 4M44 19l-4 4M19 43l4-4M44 43l-4-4"/></g></svg></div>
  <div><h3>ELECTRICAL ENGINEERING</h3><p>Provide electro-mechanical designs for machine sizing calcu-lations for motion control and fluid power applications.</p></div>
</div>
<div class="service abs" style="top:705px">
  <div class="service-icon"><svg viewBox="0 0 63 63"><circle cx="31.5" cy="31.5" r="31.5" fill="#fece3e"/><circle cx="25" cy="27" r="9" fill="none" stroke="#1b1b1b" stroke-width="6" stroke-dasharray="4 3"/><circle cx="25" cy="27" r="4" fill="#1b1b1b"/><circle cx="40" cy="39" r="6" fill="none" stroke="#1b1b1b" stroke-width="5" stroke-dasharray="3 2"/><circle cx="42" cy="22" r="4" fill="none" stroke="#1b1b1b" stroke-width="3"/></svg></div>
  <div><h3>APPLICATIONS ENGINEERING</h3><p>Provide electro-mechanical designs for machine sizing calcula-tions for motion control and fluid power applications.</p></div>
</div>
<div class="service abs" style="top:806px">
  <div class="service-icon"><svg viewBox="0 0 63 63"><circle cx="31.5" cy="31.5" r="31.5" fill="#fece3e"/><g fill="none" stroke="#1b1b1b" stroke-width="3.5"><circle cx="31.5" cy="24" r="10"/><circle cx="25" cy="36" r="10"/><circle cx="38" cy="36" r="10"/></g></svg></div>
  <div><h3>DESIGN SPECIFICATION</h3><p>Provide electro-mechanical designs for machine sizing calcula-tions for motion control and fluid power applications.</p></div>
</div>

<div class="divider abs"></div>

<section class="intro abs">
  <h2>Your Premier Automation Consulting &amp; Systems Integration choice!</h2>
  <div class="tagline">Helping your business optimize its Automation..</div>
  <p>Industrial Automation is constantly evolving with ever-changing technological breakthroughs. For companies to remain competitive, they need to be more nimble than ever implementing productivity and manufacturing innovations. But identifying and implementing the right Automation, Robotics and industrial Controls is never easy. That's where our team of experts comes in to play bringing our proven experience to the table.</p>
  <h2 class="philosophy">Our philosophy</h2>
  <p class="philosophy-text">Each situation (and company) is unique. A One-size-fits-all approach will never be the optimal solution for your business to reach its full potential. A detailed evaluation of your company's operation and a custom solution provided by VEL</p>
</section>

<section class="feature-band abs">
  <div class="feature abs" style="left:93px">
    <div class="media" role="img" aria-label="Silhouettes of business people standing before a faint world map" style="background:linear-gradient(#f3f5f7,#c9ced3)"></div>
    <div class="caption">Get to know our Team approach</div>
  </div>
  <div class="feature abs" style="left:350px">
    <div class="media" role="img" aria-label="Person facing a blue wall of sketched business strategy doodles" style="background:linear-gradient(135deg,#3f7fc9,#1c4f93)"></div>
    <div class="caption">This way to Automation success</div>
  </div>
  <div class="feature abs" style="left:608px">
    <div class="media" role="img" aria-label="Hands pointing with a pen at charts on paper" style="background:linear-gradient(135deg,#c8ced6,#eef1f4)"></div>
    <div class="caption">Bring great ideas to your business</div>
  </div>
</section>

<footer class="site-footer abs">
  <div class="footer-links abs">Home Page<span>|</span>Services<span>|</span>Contact<span>|</span>About Us</div>
  <div class="copyright abs">Content copyright 2015. VEL Engineering Solutions . All rights reserved.</div>
  <div class="brand abs"><span class="brand-dot" style="background:var(--gold)"></span>VEL</div>
</footer>

</body>
</html>
```